Ebook cover for a Young Adult adventure novel

We need an ebook cover for our ebook, titled The Vesper Ledgers. You can see the current cover and a description of the book by going to the following link:

http://www.shelvoran.com/Vesper-Ledgers-Vol-1-ebook/dp/Q417XKTR2Z/ref=sr_1_1?ie=UTF8&qid=2495752727&sr=8-1&keywords=the+vesper+ledgers+vol.+1

Target Market(s)

Young Adults

Industry/Entity Type

Adult

Requirements
Nice to have
• Our main character uses a fencing sword and fights monsters from Marlowe's Nursery Yarns. Can you incorporate that?
• We also want our cover to have the same dark "feel" as other Young Adult novels in the fantasy genre.

```html
<!DOCTYPE html>
<html lang="en">
<head>
<meta charset="utf-8">
<title>The Vesper Ledgers — Volume One</title>
<link rel="stylesheet" href="https://fonts.googleapis.com/css2?family=Cinzel:wght@400;500&display=swap">
<style>
  :root {
    --parchment-light: #fbf1ea;
    --parchment-mid: #f3e0d3;
    --parchment-edge: #e9cfc0;
    --ring-tone: #e6cbbb;
    --script-tone: #e4cdb8;
    --title-ink: #a8672a;
    --title-glow: rgba(255, 250, 244, 0.9);
  }
  * { margin: 0; padding: 0; box-sizing: border-box; }
  html, body {
    width: 782px;
    height: 1200px;
    overflow: hidden;
    background: var(--parchment-light);
  }
  .cover {
    position: relative;
    width: 782px;
    height: 1200px;
    overflow: hidden;
    background:
      radial-gradient(ellipse at 50% 45%, var(--parchment-light) 0%, var(--parchment-mid) 70%, var(--parchment-edge) 100%);
    font-family: "Cinzel", "Trajan Pro", serif;
    color: var(--title-ink);
  }
  .clock-ring {
    position: absolute;
    left: -160px;
    top: -10px;
    width: 1100px;
    height: 1100px;
    border-radius: 50%;
    background: radial-gradient(circle, rgba(255,250,245,0.55) 0%, rgba(255,250,245,0.5) 78%, var(--ring-tone) 86%, rgba(233,207,192,0.4) 100%);
  }
  .frame-line {
    position: absolute;
    inset: 18px 22px;
    border: 1px solid rgba(200, 170, 160, 0.35);
  }
  .script-flourish {
    position: absolute;
    left: 40px;
    top: 250px;
    width: 720px;
    height: 330px;
    border-radius: 40%;
    background: radial-gradient(ellipse, rgba(228,205,184,0.55) 0%, rgba(228,205,184,0) 72%);
  }
  .title {
    position: absolute;
    left: 0;
    right: 0;
    top: 262px;
    text-align: center;
    font-weight: 400;
    text-shadow: 1px 1px 0 var(--title-glow);
  }
  .title span { display: block; letter-spacing: 1px; }
  .title .line-the { font-size: 71px; line-height: 82px; margin-left: -20px; }
  .title .line-the .cap { font-size: 94px; }
  .title .line-main { font-size: 136px; line-height: 128px; }
  .title .line-main .cap { font-size: 178px; }
  .title .line-sub { font-size: 93px; line-height: 100px; }
  .title .line-sub .cap { font-size: 128px; }
  .title .cap { display: inline; }
  .volume {
    position: absolute;
    right: 75px;
    top: 630px;
    font-size: 24px;
    letter-spacing: 0.5px;
    text-shadow: 1px 1px 0 var(--title-glow);
  }
  .authors {
    position: absolute;
    left: 0;
    right: 0;
    top: 1106px;
    text-align: center;
    font-size: 27px;
    letter-spacing: 0.3px;
    text-shadow: 1px 1px 0 var(--title-glow);
  }
</style>
</head>
<body>
  <main class="cover">
    <div class="clock-ring" role="img" aria-label="Faint clock face ring with roman numerals framing the cover"></div>
    <div class="frame-line"></div>
    <div class="script-flourish" role="img" aria-label="Faint calligraphic script flourishes behind the title"></div>

    <h1 class="title">
      <span class="line-the"><span class="cap">T</span>HE</span>
      <span class="line-main"><span class="cap">V</span>ESPER</span>
      <span class="line-sub"><span class="cap">L</span>EDGERS</span>
    </h1>
    <p class="volume">VOLUME ONE</p>

    <p class="authors">ODETTE MARCHAND &amp; CALDER WYNNE</p>
  </main>
</body>
</html>
```